Designing a brochures for an educational counseling service provider

We would like a 4 sided design on a 11x8.5 paper, half folded. I have including a sample design we did to give you an idea of what we envision but we welcome creativity to make beautiful looking flyers. Text for the flier is included as well as our logo.
- The most important thing is capturing our audience/market. We will be handing these flies to schools, organizations and individual clients.

www.pvrlearningadvisors.example

Target Market(s)

We are targeting international students wanting to study in the U.S and Canada.

Industry/Entity Type

Education

Requirements
Must have
• - Clean and clear
• - Our logo should visible and well placed.
• - Could you the pictures of students, libraries and school buildings or you could use the pictures we already have.
Nice to have
• We would like this to match business cards.

```html
<!DOCTYPE html>
<html lang="en">
<head>
<meta charset="utf-8">
<title>PVR Learning Advisors – Brochure Spread</title>
<link href="https://fonts.googleapis.com/css2?family=Open+Sans:ital,wght@0,400;0,600;0,700;0,800;1,600&display=swap" rel="stylesheet">
<style>
  :root{
    --navy:#1b3a6e;
    --navy-dark:#132a52;
    --green:#7db53f;
    --green-dark:#5e9a2a;
    --sky:#4f86c6;
    --ink:#3b4452;
    --paper:#ffffff;
    --backdrop:#e6e9ee;
  }
  *{box-sizing:border-box;margin:0;padding:0}
  html,body{width:849px;height:1200px;overflow:hidden}
  body{background:var(--backdrop);font-family:"Open Sans",Arial,sans-serif;color:var(--ink);position:relative}
  .spread{position:absolute;left:0;top:272px;width:849px;height:656px;background:var(--paper);display:flex;box-shadow:0 4px 18px rgba(0,0,0,.18)}
  .page{position:relative;width:424.5px;height:656px;overflow:hidden}
  .page--inside-left{border-right:1px solid #dde2e8}
  .photo{position:absolute;left:0;width:100%}
  .photo--campus{top:0;height:200px;background:linear-gradient(160deg,#cfd8e2 0%,#8ea3b8 45%,#3e5b7e 100%)}
  .photo--students{bottom:0;height:215px;background:linear-gradient(200deg,#d9c2a3 0%,#b58a63 45%,#5d4b46 100%)}
  .wave{position:absolute;left:0;width:100%}
  .heading-about{position:absolute;top:222px;left:150px;font-size:21px;font-weight:800;color:var(--navy);letter-spacing:.5px}
  .heading-about::after{content:"";display:block;width:120px;height:3px;background:var(--green);margin-top:3px}
  .body-copy{font-size:8.6px;line-height:1.5;text-align:justify}
  .about-copy{position:absolute;top:262px;left:30px;right:30px}
  .about-copy p+p{margin-top:7px}
  .service-title{position:absolute;top:372px;left:38px;font-size:17px;font-weight:800;color:#fff;letter-spacing:.5px}
  .service-intro{position:absolute;top:410px;left:30px;right:30px;font-size:9.2px;line-height:1.45;font-weight:600;font-style:italic;color:var(--navy)}
  .package-label{position:absolute;top:456px;left:30px;background:var(--green);color:#fff;font-size:10px;font-weight:700;padding:3px 14px;border-radius:10px}
  .package-list{position:absolute;top:484px;left:30px;right:24px;display:grid;grid-template-columns:1fr 1fr;column-gap:18px;row-gap:6px;list-style:none}
  .package-list li{font-size:8.4px;line-height:1.4;padding-left:12px;position:relative}
  .package-list li::before{content:"";position:absolute;left:0;top:3px;width:6px;height:6px;border-radius:50%;background:var(--green)}
  .site-bar{position:absolute;left:0;bottom:0;width:100%;height:40px}
  .site-url{position:absolute;bottom:10px;left:0;width:100%;text-align:center;font-size:10px;font-weight:700;color:#fff;letter-spacing:.3px}
  .topic{position:absolute;left:0;right:0}
  .topic-tab{display:inline-block;background:var(--navy);color:#fff;font-size:11.5px;font-weight:700;padding:4px 24px 4px 28px;border-radius:0 14px 14px 0;border-left:6px solid var(--green)}
  .topic .body-copy{margin:7px 28px 0 28px}
  .topic--boarding{top:22px}
  .topic--college{top:118px}
  .topic--transfer{top:230px}
  .topic--scholarships{top:302px}
</style>
</head>
<body>
  <main class="spread">
    <section class="page page--inside-left">
      <div class="photo photo--campus" role="img" aria-label="Photo of a modern university library interior"></div>
      <svg class="wave" style="top:165px" width="425" height="60" viewBox="0 0 425 60" aria-hidden="true">
        <path d="M0 22 Q210 -6 425 26 L425 60 L0 60 Z" fill="var(--green)"/>
        <path d="M0 32 Q210 6 425 36 L425 60 L0 60 Z" fill="var(--navy)"/>
        <path d="M0 42 Q210 18 425 46 L425 60 L0 60 Z" fill="var(--paper)"/>
      </svg>
      <h2 class="heading-about">ABOUT US:</h2>
      <div class="about-copy body-copy">
        <p>Our mission is to make quality education accessible and affordable to families around the world. We guide students through every step of choosing and applying to schools abroad, so the journey feels clear and calm.</p>
        <p>We are a family-owned organization that works with parents and students to find the right fit for every learner. Our advisors know schools in the United States and Canada and share honest, practical advice.</p>
      </div>
      <svg class="wave" style="top:362px" width="425" height="40" viewBox="0 0 425 40" aria-hidden="true">
        <path d="M0 4 L300 4 Q340 4 360 20 Q380 36 425 36 L425 40 L0 40 Z" fill="var(--green)"/>
        <path d="M0 0 L290 0 Q330 0 350 16 Q370 32 425 32 L425 36 L0 36 Z" fill="var(--navy)"/>
      </svg>
      <h2 class="service-title">OUR SERVICE</h2>
      <p class="service-intro">Finding the right school or program for your child is one of the most important decisions your family will make. The right choice will make a great impact on your child's future.</p>
      <span class="package-label">Our package includes:</span>
      <ul class="package-list">
        <li>Interview sessions</li>
        <li>Assistance with application and essays</li>
        <li>Present range of options based on needs and goals of the family</li>
        <li>Guidance on student progress throughout their enrollment with the school</li>
        <li>Interview coaching</li>
        <li>Advice on scholarships and visas</li>
      </ul>
      <svg class="site-bar" width="425" height="40" viewBox="0 0 425 40" aria-hidden="true">
        <path d="M0 8 Q212 -4 425 8 L425 40 L0 40 Z" fill="var(--green)"/>
        <path d="M0 12 Q212 2 425 12 L425 40 L0 40 Z" fill="var(--navy)"/>
      </svg>
      <p class="site-url">www.pvrlearningadvisors.example</p>
    </section>

    <section class="page page--inside-right">
      <article class="topic topic--boarding">
        <h3 class="topic-tab">Boarding schools:</h3>
        <p class="body-copy">Boarding schools offer students a structured day, small classes and close attention from teachers. We help families compare programs, arrange campus visits and prepare strong applications for admission.</p>
      </article>
      <article class="topic topic--college">
        <h3 class="topic-tab">College admissions:</h3>
        <p class="body-copy">At PVR Learning Advisors we help students plan their path to college. We review course choices, test dates and deadlines, and support every essay and interview so each application shows the student at their best.</p>
      </article>
      <article class="topic topic--transfer">
        <h3 class="topic-tab">Transfer students:</h3>
        <p class="body-copy">Need to move to another school or program? We help students transfer smoothly and keep their credits and goals on track.</p>
      </article>
      <article class="topic topic--scholarships">
        <h3 class="topic-tab">Scholarships:</h3>
        <p class="body-copy">Paying for education can be a heavy load. Our team helps families find scholarships and financial aid and prepare complete, timely applications that give every student a fair chance.</p>
      </article>
      <div class="photo photo--students" role="img" aria-label="Photo of smiling students together on campus"></div>
      <svg class="wave" style="bottom:175px" width="425" height="50" viewBox="0 0 425 50" aria-hidden="true">
        <path d="M0 0 L425 0 L425 22 Q210 52 0 26 Z" fill="var(--paper)"/>
        <path d="M0 26 Q210 52 425 22 L425 30 Q210 60 0 34 Z" fill="var(--green)"/>
        <path d="M0 34 Q210 60 425 30 L425 36 Q210 66 0 40 Z" fill="var(--navy)"/>
      </svg>
    </section>
  </main>
</body>
</html>
```